Website needed for modern mobile app developer for small business'

Hi

We are looking for someone to design a very modern looking website with company logo that outlines what our business is and let's users purchase a mobile app designed by our company. (For ideas think quillnest.example or ) The user should be able to describe what functionality they require and we will go and provide a test version of their app built

We would also like a testimonials page.

I currently have hosting on Brindle Hosting, so if this could be taken into account that would be great.
Updates

here is the logo - if colour scheme could match that would be great Added Wednesday, March 30, 2016

Target Market(s)

Small and medium business

Industry/Entity Type

Business

Number of Pages Required

3 page

Requirements
Must have
• Homepage who we are and what we offer
• Pricing page explaining the different products available - HTML5 app, Robotix App or Pocketphone app with an option to purchase
• A testimonials page
• A one that makes it easier for potential customers to get in contact.

```html
<!DOCTYPE html>
<html lang="en">
<head>
<meta charset="utf-8">
<title>ventlo — mobile app developer</title>
<link rel="stylesheet" href="https://fonts.googleapis.com/css2?family=Raleway:ital,wght@0,300;0,400;0,500;0,600;0,700;1,400&display=swap">
<style>
:root{
  --ink:#2b2b2b;
  --text:#555555;
  --muted:#8a8a8a;
  --blue:#1e88d6;
  --green:#4aa81a;
  --line:#e4e4e4;
  --band:#f2f2f2;
  --white:#ffffff;
  --dark:#2c2622;
  --star:#f5b400;
}
*{box-sizing:border-box;margin:0;padding:0}
html,body{width:1200px;height:2917px;overflow:hidden}
body{position:relative;background:var(--white);font-family:'Raleway',sans-serif;color:var(--text)}
.abs{position:absolute}

/* header */
.site-header{position:absolute;left:0;top:0;width:1200px;height:70px;background:var(--white)}
.brand{left:74px;top:18px;font-size:30px;font-weight:600;color:var(--ink);letter-spacing:.5px}
.main-nav{left:543px;top:26px;display:flex;gap:0;font-size:15px;font-weight:500;color:var(--ink)}
.main-nav a{color:inherit;text-decoration:none;margin-right:48px}
.main-nav a.active{color:var(--blue)}
.social{left:982px;top:30px;display:flex;gap:17px}
.social span{width:11px;height:11px;border-radius:50%;background:var(--ink);display:block}

/* hero */
.hero{left:0;top:70px;width:1200px;height:537px;background:linear-gradient(135deg,#8d8882 0%,#5d6471 40%,#4c5262 60%,#7a5850 85%,#b3aaa2 100%)}
.hero-title{left:0;top:200px;width:1200px;text-align:center;color:var(--white);font-size:53px;font-weight:400;line-height:60px}
.hero-dots{left:556px;top:465px;display:flex;gap:11px}
.hero-dots span{width:13px;height:13px;border-radius:50%;background:var(--white)}
.hero-dots span.on{background:var(--blue)}

/* sections */
h2{font-weight:400;color:var(--ink);font-size:35px}
.copy{font-size:16.5px;line-height:30px;color:var(--text)}
.btn-outline{display:block;border:1.5px solid var(--blue);border-radius:23px;color:var(--blue);font-size:16px;text-align:center;line-height:42px;height:45px}
.who-image{left:74px;top:671px;width:422px;height:292px;background:radial-gradient(circle at 60% 35%,#c9d8ee 0%,#e9eef6 45%,#f7f7f7 75%)}
.divider{left:74px;top:1017px;width:1052px;height:1px;background:var(--line)}

.feature-icon{width:80px;height:80px;border:2px solid #bdbdbd;border-radius:50%;display:flex;align-items:center;justify-content:center}
.feature-title{font-size:16px;font-weight:600;color:var(--blue)}
.feature-copy{font-size:14px;line-height:25px;color:var(--text)}

/* pricing */
.pricing{left:0;top:1426px;width:1200px;height:523px;background:var(--band)}
.section-title{width:1200px;left:0;text-align:center;font-size:35px;font-weight:400;color:var(--ink)}
.plan{width:330px;text-align:center}
.plan-icon{width:150px;height:150px;margin:0 auto;border:3px solid #cfcfcf;border-radius:50%;background:var(--white);display:flex;align-items:center;justify-content:center}
.plan-title{margin-top:25px;font-size:22px;font-weight:500;color:var(--blue)}
.plan-copy{margin:10px auto 0;width:285px;font-size:14.5px;line-height:25px;color:var(--ink)}
.btn-buy{display:block;margin:28px auto 0;width:154px;height:43px;border-radius:22px;background:var(--green);color:var(--white);font-size:14px;font-weight:500;line-height:43px}

/* testimonials */
.quote-card{width:513px;height:154px;background:linear-gradient(#f1f1f1,#ffffff 60%);box-shadow:0 1px 4px rgba(0,0,0,.08);padding:28px 50px;text-align:center;font-size:14px;font-style:italic;line-height:25px;color:var(--text)}
.quote-tail{width:24px;height:24px;background:var(--white);transform:rotate(45deg);box-shadow:2px 2px 3px rgba(0,0,0,.05)}
.author{width:513px;text-align:center}
.stars{color:var(--star);font-size:17px;letter-spacing:1px}
.author-name{font-size:16px;font-weight:600;color:var(--blue);margin-top:4px}
.author-place{font-size:11px;font-style:italic;color:var(--muted);margin-top:4px}
.quote-dots{left:586px;top:2336px;display:flex;gap:8px}
.quote-dots span{width:10px;height:10px;border-radius:50%;background:#b5b5b5}
.quote-dots span.on{background:#444}

/* contact */
.contact{left:0;top:2392px;width:1200px;height:382px;background:linear-gradient(120deg,#3a332d 0%,#2a2420 45%,#3b2f28 75%,#4a3d33 100%)}
.field{height:38px;border:1.5px solid #cfcfcf;border-radius:3px;color:#e9e9e9;font-size:14px;padding:9px 15px}
.btn-submit{left:515px;top:2688px;width:168px;height:45px;border:1.5px solid var(--blue);border-radius:23px;color:var(--blue);font-size:16px;text-align:center;line-height:42px}

/* footer */
.footer-nav{left:0;top:2817px;width:1200px;display:flex;justify-content:center;gap:52px;font-size:15px;color:var(--ink)}
.copyright{left:0;top:2853px;width:1200px;text-align:center;font-size:12.5px;color:var(--muted)}
</style>
</head>
<body>

<header class="site-header">
  <div class="abs brand">ventlo</div>
  <nav class="abs main-nav">
    <a class="active" href="#">Home</a>
    <a href="#">Pricing</a>
    <a href="#">Testimonials</a>
    <a href="#">Contact Us</a>
  </nav>
  <div class="abs social" aria-label="Social links"><span></span><span></span><span></span><span></span><span></span></div>
</header>

<section class="abs hero" role="img" aria-label="Photo of two colleagues working together at a laptop in a bright office">
</section>
<h1 class="abs hero-title">We are a mobile app developer for<br>small business &amp; enterprises</h1>
<div class="abs hero-dots"><span class="on"></span><span></span><span></span><span></span></div>

<!-- who we are -->
<div class="abs who-image" role="img" aria-label="Illustration of hands holding phones with app icons flying between them"></div>
<h2 class="abs" style="left:548px;top:678px">Who we are</h2>
<p class="abs copy" style="left:548px;top:734px;width:560px">Aenean a nibh eget turpis vehicula tempus ac sed massa. Vestibulum dolor nulla, ultrices ac tincidunt sed, laoreet non est. Suspendisse lobortis turpis in odio blandit ac interdum lorem euismod. Etiam risus massa, vulputate eu pellentesque et, consectetur a neque.</p>
<a class="abs btn-outline" style="left:548px;top:893px;width:167px">Read More</a>

<div class="abs divider"></div>

<!-- what we offer -->
<h2 class="abs" style="left:74px;top:1083px">What we offer</h2>
<p class="abs copy" style="left:74px;top:1142px;width:500px">Aenean a nibh eget turpis vehicula tempus ac sed massa. Vestibulum dolor nulla, ultrices ac tincidunt sed, laoreet non est. Suspendisse lobortis turpis in odio blandit ac interdum lorem euismod.</p>
<a class="abs btn-outline" style="left:74px;top:1299px;width:169px">Read More</a>

<div class="abs feature-icon" style="left:615px;top:1061px">
  <svg width="34" height="26" viewBox="0 0 34 26"><path d="M1 1V25H33" fill="none" stroke="#2b2b2b" stroke-width="2"/><path d="M4 23V14L11 6L17 13L22 9L30 15V23Z" fill="#2b2b2b"/></svg>
</div>
<div class="abs" style="left:714px;top:1059px;width:420px">
  <div class="feature-title">Scan Your Market Report</div>
  <div class="feature-copy" style="margin-top:6px">Aenean a nibh eget turpis vehicula tempus ac sed massa. Vestibulum dolor nulla, ultrices ac tincidunt sed..</div>
</div>

<div class="abs feature-icon" style="left:615px;top:1176px">
  <svg width="36" height="30" viewBox="0 0 36 30"><circle cx="18" cy="8" r="6" fill="#2b2b2b"/><circle cx="7" cy="11" r="4.5" fill="#2b2b2b"/><circle cx="29" cy="11" r="4.5" fill="#2b2b2b"/><path d="M9 29C9 20 13 16 18 16S27 20 27 29Z" fill="#2b2b2b"/><path d="M0 27C0 21 3 18 7 18C9 18 10 19 10 19C8 22 7.5 25 7.5 27Z" fill="#2b2b2b"/><path d="M36 27C36 21 33 18 29 18C27 18 26 19 26 19C28 22 28.5 25 28.5 27Z" fill="#2b2b2b"/></svg>
</div>
<div class="abs" style="left:714px;top:1175px;width:420px">
  <div class="feature-title">Staff Management</div>
  <div class="feature-copy" style="margin-top:6px">Aenean a nibh eget turpis vehicula tempus ac sed massa. Vestibulum dolor nulla, ultrices ac tincidunt sed..</div>
</div>

<div class="abs feature-icon" style="left:615px;top:1293px">
  <svg width="24" height="34" viewBox="0 0 24 34"><rect x="1" y="1" width="22" height="32" rx="2" fill="#2b2b2b"/><g fill="#fff"><rect x="5" y="5" width="4" height="4"/><rect x="10" y="5" width="4" height="4"/><rect x="15" y="5" width="4" height="4"/><rect x="5" y="11" width="4" height="4"/><rect x="10" y="11" width="4" height="4"/><rect x="15" y="11" width="4" height="4"/><rect x="5" y="17" width="4" height="4"/><rect x="10" y="17" width="4" height="4"/><rect x="15" y="17" width="4" height="4"/><rect x="9" y="25" width="6" height="8"/></g></svg>
</div>
<div class="abs" style="left:714px;top:1291px;width:420px">
  <div class="feature-title">Manage Your Company</div>
  <div class="feature-copy" style="margin-top:6px">Aenean a nibh eget turpis vehicula tempus ac sed massa. Vestibulum dolor nulla, ultrices ac tincidunt sed..</div>
</div>

<!-- pricing -->
<section class="abs pricing"></section>
<h2 class="abs section-title" style="top:1466px">Pricing</h2>

<div class="abs plan" style="left:74px;top:1545px">
  <div class="plan-icon"><svg width="50" height="50"><rect x="5" y="5" width="40" height="40" rx="4" fill="var(--blue)"/></svg></div>
  <div class="plan-title">HTML5 App</div>
  <p class="plan-copy">Aenean a nibh eget turpis vehicula tempus ac sed massa. Vestibulum dolor nulla, ultrices ac tincidunt sed..</p>
  <a class="btn-buy">Purchase &nbsp;Now</a>
</div>
<div class="abs plan" style="left:434px;top:1545px">
  <div class="plan-icon"><svg width="50" height="50"><circle cx="25" cy="25" r="21" fill="var(--blue)"/></svg></div>
  <div class="plan-title">Robotix App</div>
  <p class="plan-copy">Aenean a nibh eget turpis vehicula tempus ac sed massa. Vestibulum dolor nulla, ultrices ac tincidunt sed..</p>
  <a class="btn-buy">Purchase &nbsp;Now</a>
</div>
<div class="abs plan" style="left:794px;top:1545px">
  <div class="plan-icon"><svg width="50" height="50"><circle cx="25" cy="25" r="21" fill="var(--blue)"/></svg></div>
  <div class="plan-title">Pocketphone App</div>
  <p class="plan-copy">Aenean a nibh eget turpis vehicula tempus ac sed massa. Vestibulum dolor nulla, ultrices ac tincidunt sed..</p>
  <a class="btn-buy">Purchase &nbsp;Now</a>
</div>

<!-- testimonials -->
<h2 class="abs section-title" style="top:1981px">Testimonials</h2>

<div class="abs quote-tail" style="left:318px;top:2194px"></div>
<blockquote class="abs quote-card" style="left:74px;top:2052px">" Aliquam molestie, mi et imperdiet euismod, dui purus auctor tellus, et interdum lacus lectus et ante. Sed accumsan sollicitudin sapien, sit amet adipiscing turpis gravida ac. Vivamus egestas risus in magna varius commodo.."</blockquote>
<div class="abs author" style="left:74px;top:2243px">
  <div class="stars">★★★★★</div>
  <div class="author-name">Name Heading</div>
  <div class="author-place">Location</div>
</div>

<div class="abs quote-tail" style="left:859px;top:2194px"></div>
<blockquote class="abs quote-card" style="left:615px;top:2052px">" Aliquam molestie, mi et imperdiet euismod, dui purus auctor tellus, et interdum lacus lectus et ante. Sed accumsan sollicitudin sapien, sit amet adipiscing turpis gravida ac. Vivamus egestas risus in magna varius commodo.."</blockquote>
<div class="abs author" style="left:615px;top:2243px">
  <div class="stars">★★★★★</div>
  <div class="author-name">Name Heading</div>
  <div class="author-place">Location</div>
</div>

<div class="abs quote-dots"><span class="on"></span><span></span></div>

<!-- contact -->
<section class="abs contact" role="img" aria-label="Dark blurred photo of hands holding a smartphone"></section>
<h2 class="abs section-title" style="top:2423px;color:var(--white)">Quick Contact</h2>
<div class="abs field" style="left:255px;top:2493px;width:330px">Name</div>
<div class="abs field" style="left:615px;top:2493px;width:332px">Email Address</div>
<div class="abs field" style="left:255px;top:2542px;width:330px">Phone Number</div>
<div class="abs field" style="left:615px;top:2542px;width:332px">Subject</div>
<div class="abs field" style="left:255px;top:2593px;width:692px;height:65px">Message</div>
<div class="abs btn-submit">Submit</div>

<!-- footer -->
<nav class="abs footer-nav"><span>Home</span><span>Pricing</span><span>Testimonials</span><span>Contact Us</span></nav>
<p class="abs copyright">Copyright ©2016 Company Name All Right Reserved</p>

</body>
</html>
```